Millcrest PTA Website Design

We are working with Millcrest Elementary School PTA. They are a Parent Teacher Association that needs a new website design.

A Parent Teacher Association (PTA) is a volunteer organization that brings parents, teachers, and school staff together to support students and enhance their educational experience. PTAs organize fundraisers, sponsor school events, advocate for education policies, and foster stronger connections between families and schools.

Some sites to use for inspiration:

https://parentboardhub.com/demo/
https://nonprofits.kindlyfundr.com/blogs/more-great-pta-websites-you-should-copy
https://www.rvmxpta.com

Thank you for taking the time to consider designing a website for us. We are web developers based in Stockton and Los Angeles, CA, USA. Most of our projects go through the same process. Understanding this process may help you win a project with us. We custom-code all of our websites in-house. We don’t have any requirements as to what tools you use for your design, but we prefer Figma files. For any design that we label as four-stars, we send it to the client for review. The client picks the final design they want us to use. Once we complete this process, we will continue to show additional clients all the four-star sites and purchase them later. Your designs will have multiple chances to sell. For better chances of success, we ask that you follow these guidelines.

IMAGES:
If you use any images or icons in the design, we ask that you have a link to the asset so we can purchase the image/icon. Most of the designs we submit do not have the customer’s images on them unless they have some great images. Be creative; show us the feeling you are trying to portray with your image choices. Use any royalty-free site you choose. We subscribe to Adobe and mainly use their images, but we can purchase images outside of Adobe.

PLEASE NOTE: we will not submit designs to clients with watermarks on the images.

FONTS:
We ask that you identify the fonts used in the design. This can be done in a message if you want. We typically use Google Fonts and Adobe Fonts.

CONTENT:
We're always open to different content and ideas. We often submit designs with stock images so the client can see our vision. We typically take pictures after the website launch to use their images with our vision. Lorem Ipsum is fine for paragraphs, but we ask that you write the headers in correct English. We want to be able to show the vision and identify the sections of the website.

INSPIRATION:
We typically add a couple of links in the brief of websites we like to help you get started in your design.

REVISIONS:
We do not often ask for revisions of the designs unless we see something in the design that may not appeal to the client. If there are slight changes that we want to make, we do that in the development process.

FEEDBACK:
We rarely give feedback on designs during the design process. We are working on many website projects and do not have the time to provide feedback. We usually respond if your request is well thought out and asks specific questions, but a note asking “feedback, please” usually goes unanswered.

```html
<!DOCTYPE html>
<html lang="en">
<head>
<meta charset="utf-8">
<title>Millcrest Blue and White</title>
<link href="https://fonts.googleapis.com/css2?family=Roboto:wght@400;500;700&family=Roboto+Slab:wght@700;800&display=swap" rel="stylesheet">
<style>
:root{
  --blue:#243f8c;
  --ink:#1d1d1d;
  --text:#4a4a4a;
  --line:#cfcfcf;
  --panel:#f1f1f1;
  --footer:#161616;
  --white:#ffffff;
  --gold:#f0b81c;
}
*{box-sizing:border-box;margin:0;padding:0}
html,body{width:1200px;height:2458px;overflow:hidden}
body{position:relative;background:var(--white);font-family:"Roboto",Arial,sans-serif;color:var(--text)}
.abs{position:absolute}
.slab{font-family:"Roboto Slab",Georgia,serif;font-weight:800}
.hero{left:0;top:0;width:1200px;height:480px;background:linear-gradient(120deg,#6f6a63 0%,#8e8077 30%,#2f7f95 55%,#4c6c78 75%,#3b3b3b 100%)}
.brand{left:144px;top:40px;display:flex;align-items:center;gap:10px;color:var(--white);font-weight:700;font-size:24px}
.brand-mark{width:22px;height:22px;background:var(--white)}
.hero-title{left:143px;top:396px;font-size:35px;color:var(--white);letter-spacing:.2px}
.nav{left:0;top:480px;width:1200px;height:56px;background:var(--blue);display:flex;justify-content:center;align-items:center;font-size:13px;font-weight:700;color:var(--white)}
.nav .sep{margin:0 14px;font-weight:400}
.side-box{left:24px;width:339px;border:1px solid var(--line);padding:13px 13px 0}
.side-head{height:49px;background:var(--blue);color:var(--white);font-size:24px;font-weight:500;display:flex;align-items:center;justify-content:center}
.contact-row{display:flex;gap:12px;padding-left:13px;margin-top:36px}
.contact-row.first{margin-top:38px}
.ic{width:42px;height:42px;border-radius:50%;background:var(--blue);flex:none;display:flex;align-items:center;justify-content:center;margin-top:4px}
.contact-row b{display:block;color:var(--ink);font-size:19px;font-weight:500;margin-bottom:1px}
.contact-row p{font-size:15.5px;color:var(--ink);line-height:24px}
.map{margin:28px 16px 0 17px;height:196px;background:linear-gradient(135deg,#e7ebee,#dde6df 60%,#cfe6da)}
.link-list{list-style:none;padding:18px 18px 0 13px}
.link-list li{display:flex;align-items:flex-start;gap:14px;font-size:17.5px;color:var(--ink);padding:11px 0 12px;border-bottom:1px solid var(--line);line-height:24px}
.link-list li:last-child{border-bottom:none}
.tick{width:14px;height:14px;flex:none;margin-top:5px}
.welcome{left:400px;top:572px;width:760px}
.welcome h1{font-size:32px;line-height:41px;color:var(--ink)}
.rule{width:111px;height:2px;background:var(--blue);margin:13px 0 15px}
.welcome p{font-size:15.5px;line-height:24px;margin-bottom:24px}
.card{width:238px;display:flex;flex-direction:column}
.card.row1{height:382px}
.card.row2{height:363px}
.card .ph{height:187px;flex:none}
.card h3{font-size:19.5px;font-weight:500;color:var(--ink);line-height:24px;margin-top:14px}
.card p{font-size:15.5px;line-height:24px;margin-top:14px;padding-right:4px}
.card.row2 p{margin-top:6px}
.more{align-self:flex-start;margin-top:auto;display:inline-flex;align-items:center;gap:4px;font-size:17.5px;font-weight:500;color:var(--ink);border-bottom:2px solid var(--blue);padding-bottom:1px}
.cta{left:402px;top:1780px;width:751px;height:230px;background:var(--panel);border:3px solid #dedede;text-align:center}
.cta h2{font-size:19px;color:var(--ink);margin-top:44px}
.cta p{font-size:15.5px;line-height:24px;margin:6px auto 0;width:590px}
.btn{display:inline-block;margin-top:13px;background:var(--blue);color:var(--white);font-size:15px;font-weight:500;padding:13px 23px}
.footer{left:0;top:2084px;width:1200px;height:374px;background:var(--footer);color:var(--white)}
.f-title{font-size:21px;font-weight:700;line-height:28px;letter-spacing:.2px}
.subscribe{left:175px;top:66px}
.email-input{margin-top:20px;width:271px;height:43px;border:1px solid #555;display:flex;align-items:center;justify-content:space-between;padding:0 10px 0 17px;font-size:13px}
.socials{display:flex;gap:6px;margin-top:23px}
.socials span{width:27px;height:27px;border-radius:50%;background:#2b2b2b}
.socials span.on{background:var(--white)}
.cinfo{left:487px;top:66px}
.ci-row{display:flex;gap:21px;margin-top:16px}
.ci-row.first{margin-top:18px}
.ci-row svg{flex:none;margin-top:4px}
.ci-row b{display:block;font-size:16.5px;font-weight:500;margin-bottom:2px}
.ci-row p{font-size:14px;line-height:16px}
.qlinks{left:757px;top:66px}
.ql-cols{display:flex;gap:56px;margin-top:24px}
.ql-cols ul{list-style:none}
.ql-cols li{font-size:16.5px;margin-bottom:12px;display:flex;align-items:center;gap:12px}
.f-rule{left:171px;top:302px;width:858px;height:1px;background:#444}
.f-legal{left:170px;top:327px;font-size:15px}
.f-copy{left:776px;top:327px;font-size:15px}
</style>
</head>
<body>

<div class="abs hero" role="img" aria-label="Photo of smiling volunteers in teal shirts joining hands in a team huddle"></div>
<div class="abs brand"><span class="brand-mark"></span>Millcrest</div>
<div class="abs hero-title slab">MILLCREST BLUE AND WHITE</div>

<nav class="abs nav">
  <span>PTA and YOU!</span><span class="sep">|</span>
  <span>Millcrest PTA Store</span><span class="sep">|</span>
  <span>PTA-Funded Progams</span><span class="sep">|</span>
  <span>Blue and White</span><span class="sep">|</span>
  <span>Contact Us</span><span class="sep">|</span>
  <span>Millcrest PTA on Townboard</span><span class="sep">|</span>
  <span>Millcrest Elementary Website</span>
</nav>

<aside class="abs side-box" style="top:577px;height:603px">
  <div class="side-head">CONTACT US</div>
  <div class="contact-row first">
    <span class="ic"><svg width="14" height="14" viewBox="0 0 24 24"><path fill="#fff" d="M6.6 10.8a15 15 0 0 0 6.6 6.6l2.2-2.2c.3-.3.7-.4 1-.2 1.1.4 2.3.6 3.6.6.6 0 1 .4 1 1V20c0 .6-.4 1-1 1A17 17 0 0 1 3 4c0-.6.4-1 1-1h3.5c.6 0 1 .4 1 1 0 1.3.2 2.5.6 3.6.1.3 0 .7-.2 1z"/></svg></span>
    <div><b>Email</b><p>hello@millcrestpta.org</p></div>
  </div>
  <div class="contact-row">
    <span class="ic"><svg width="14" height="14" viewBox="0 0 24 24"><path fill="#fff" d="M6.6 10.8a15 15 0 0 0 6.6 6.6l2.2-2.2c.3-.3.7-.4 1-.2 1.1.4 2.3.6 3.6.6.6 0 1 .4 1 1V20c0 .6-.4 1-1 1A17 17 0 0 1 3 4c0-.6.4-1 1-1h3.5c.6 0 1 .4 1 1 0 1.3.2 2.5.6 3.6.1.3 0 .7-.2 1z"/></svg></span>
    <div><b>Phone</b><p>(555)014-2760</p></div>
  </div>
  <div class="contact-row">
    <span class="ic"><svg width="14" height="14" viewBox="0 0 24 24"><path fill="#fff" d="M6.6 10.8a15 15 0 0 0 6.6 6.6l2.2-2.2c.3-.3.7-.4 1-.2 1.1.4 2.3.6 3.6.6.6 0 1 .4 1 1V20c0 .6-.4 1-1 1A17 17 0 0 1 3 4c0-.6.4-1 1-1h3.5c.6 0 1 .4 1 1 0 1.3.2 2.5.6 3.6.1.3 0 .7-.2 1z"/></svg></span>
    <div><b>Address</b><p>418 Orchard Bend Way<br>Fairhaven, CA 90210</p></div>
  </div>
  <div class="map" role="img" aria-label="Street map showing the school location"></div>
</aside>

<aside class="abs side-box" style="top:1209px;height:421px">
  <div class="side-head">USEFUL LINKS</div>
  <ul class="link-list">
    <li><svg class="tick" viewBox="0 0 16 16"><circle cx="8" cy="8" r="8" fill="#243f8c"/><path d="M4.5 8.2l2.3 2.2 4.7-4.6" stroke="#fff" stroke-width="2" fill="none"/></svg>PTA and YOU!</li>
    <li><svg class="tick" viewBox="0 0 16 16"><circle cx="8" cy="8" r="8" fill="#243f8c"/><path d="M4.5 8.2l2.3 2.2 4.7-4.6" stroke="#fff" stroke-width="2" fill="none"/></svg>Millcrest PTA Store</li>
    <li><svg class="tick" viewBox="0 0 16 16"><circle cx="8" cy="8" r="8" fill="#243f8c"/><path d="M4.5 8.2l2.3 2.2 4.7-4.6" stroke="#fff" stroke-width="2" fill="none"/></svg>PTA-Funded Progams</li>
    <li><svg class="tick" viewBox="0 0 16 16"><circle cx="8" cy="8" r="8" fill="#243f8c"/><path d="M4.5 8.2l2.3 2.2 4.7-4.6" stroke="#fff" stroke-width="2" fill="none"/></svg>Blue and White</li>
    <li><svg class="tick" viewBox="0 0 16 16"><circle cx="8" cy="8" r="8" fill="#243f8c"/><path d="M4.5 8.2l2.3 2.2 4.7-4.6" stroke="#fff" stroke-width="2" fill="none"/></svg>Contact Us</li>
    <li><svg class="tick" viewBox="0 0 16 16"><circle cx="8" cy="8" r="8" fill="#243f8c"/><path d="M4.5 8.2l2.3 2.2 4.7-4.6" stroke="#fff" stroke-width="2" fill="none"/></svg>Millcrest PTA on Townboard</li>
    <li><svg class="tick" viewBox="0 0 16 16"><circle cx="8" cy="8" r="8" fill="#243f8c"/><path d="M4.5 8.2l2.3 2.2 4.7-4.6" stroke="#fff" stroke-width="2" fill="none"/></svg>Millcrest Elementary Website</li>
  </ul>
</aside>

<aside class="abs side-box" style="top:1661px;height:254px">
  <div class="side-head">RECENT POSTS</div>
  <ul class="link-list">
    <li><svg class="tick" viewBox="0 0 16 16"><circle cx="8" cy="8" r="8" fill="#243f8c"/><path d="M4.5 8.2l2.3 2.2 4.7-4.6" stroke="#fff" stroke-width="2" fill="none"/></svg>Reflections Art Program</li>
    <li><svg class="tick" viewBox="0 0 16 16"><circle cx="8" cy="8" r="8" fill="#243f8c"/><path d="M4.5 8.2l2.3 2.2 4.7-4.6" stroke="#fff" stroke-width="2" fill="none"/></svg>Welcome Back!</li>
    <li><svg class="tick" viewBox="0 0 16 16"><circle cx="8" cy="8" r="8" fill="#243f8c"/><path d="M4.5 8.2l2.3 2.2 4.7-4.6" stroke="#fff" stroke-width="2" fill="none"/></svg>Yee-haw! Get dem tickets here, little dogie!</li>
  </ul>
</aside>

<section class="abs welcome">
  <h1 class="slab">WELCOME TO<br>MILLCREST BLUE AND WHITE</h1>
  <div class="rule"></div>
  <p>Don't be caught unprepared! Join PTA and make a difference.<br>Yearbooks are where it's at!&nbsp; Snap those photos of school events and fun days at Millcrest then send them over to yearbook@millcrestpta.org!</p>
  <p>Also, you can't leave home without your Millcrest Spirit Wear! Choose your style and size below then check out using your credit/debit card or QuickPurse. We can't wait to see you show off your Lion Pride...even if it's only virtually right now!</p>
  <p>Our ordering window for 2022-2023 has officially closed!&nbsp; Did you miss it?&nbsp; Please contact Dana Whitfield at hello@millcrestpta.org to inquire about our instock inventory.</p>
</section>

<div class="abs card row1" style="left:400px;top:957px">
  <div class="ph" role="img" aria-label="Photo of volunteers chatting outdoors in autumn" style="background:linear-gradient(135deg,#b58a55,#8c6a45 50%,#d9a441)"></div>
  <h3>Give Back!</h3>
  <p>PTA works hard to provide an incredible array of programs and experiences for all our Millcrest Lions!</p>
  <span class="more">Learn More <svg width="10" height="14" viewBox="0 0 10 14"><path d="M2 1l6 6-6 6" stroke="#243f8c" stroke-width="2.5" fill="none"/></svg></span>
</div>
<div class="abs card row1" style="left:658px;top:957px">
  <div class="ph" role="img" aria-label="Illustration of colourful hands circling a globe" style="background:linear-gradient(135deg,#e9e9e9,#cfd8e0 50%,#e7c9c9)"></div>
  <h3>PTA Membership and Meetings</h3>
  <p>Interested in joining?&nbsp; Joining Millcrest PTA online is as simple as a 1-2-3...or A-B-C! Join us here!!</p>
  <span class="more">Learn More <svg width="10" height="14" viewBox="0 0 10 14"><path d="M2 1l6 6-6 6" stroke="#243f8c" stroke-width="2.5" fill="none"/></svg></span>
</div>
<div class="abs card row1" style="left:915px;top:957px">
  <div class="ph" role="img" aria-label="Photo of hands holding up a globe against the sky" style="background:linear-gradient(160deg,#8fb6c4,#4f8f9f 55%,#2f6e5a)"></div>
  <h3>2024 Fall Carnival</h3>
  <p>Join the fun and support the Millcrest 6th Graders! Carnival games, tasty food, yummy treats and loads of fun</p>
  <span class="more">Learn More <svg width="10" height="14" viewBox="0 0 10 14"><path d="M2 1l6 6-6 6" stroke="#243f8c" stroke-width="2.5" fill="none"/></svg></span>
</div>

<div class="abs card row2" style="left:400px;top:1380px">
  <div class="ph" role="img" aria-label="Photo of students reviewing a clipboard together" style="background:linear-gradient(135deg,#4d78b8,#d8d3c8 55%,#3f5f86)"></div>
  <h3>Volunteer with PTA!</h3>
  <p>Become a PTA volunteer today! Join the Board...Plan an activity or event... Help in the classroom...</p>
  <span class="more">Learn More <svg width="10" height="14" viewBox="0 0 10 14"><path d="M2 1l6 6-6 6" stroke="#243f8c" stroke-width="2.5" fill="none"/></svg></span>
</div>
<div class="abs card row2" style="left:658px;top:1380px">
  <div class="ph" role="img" aria-label="Photo of children giving thumbs up" style="background:linear-gradient(135deg,#7d8f6a,#c9a08c 50%,#9a3b46)"></div>
  <h3>Millcrest Yearbook</h3>
  <p>Parents, students, family and friends!&nbsp; Break out that camera and snap those pics!&nbsp; 1st day of school, Red Ribbon Week, Spirit</p>
  <span class="more">Learn More <svg width="10" height="14" viewBox="0 0 10 14"><path d="M2 1l6 6-6 6" stroke="#243f8c" stroke-width="2.5" fill="none"/></svg></span>
</div>
<div class="abs card row2" style="left:915px;top:1380px">
  <div class="ph" role="img" aria-label="Photo of students picking up litter in a park" style="background:linear-gradient(135deg,#8a5a3c,#4b4f7a 50%,#6f8a5a)"></div>
  <h3>Important DAtes</h3>
  <p>Don't miss out on important PTA events throughout the year!&nbsp; Stay tuned for important 2022-2023 dates!</p>
  <span class="more">Learn More <svg width="10" height="14" viewBox="0 0 10 14"><path d="M2 1l6 6-6 6" stroke="#243f8c" stroke-width="2.5" fill="none"/></svg></span>
</div>

<section class="abs cta">
  <h2 class="slab">MAKE A DIFFERENCE TODAY</h2>
  <p>Lorem ipsum dolor sit amet, consectetur adipiscing elit, sed do eiusmod tempor exercitation ullamco laboris nisi ut aliquip ex ea commodo consequat.</p>
  <span class="btn">Donate Now</span>
</section>

<footer class="abs footer">
  <div class="abs subscribe">
    <div class="f-title">SUBSCRIBE TO<br>OUR NEWSLETTER</div>
    <div class="email-input">Email address <svg width="14" height="14" viewBox="0 0 16 16"><path d="M1 8L15 1 11 15 8 9z" fill="#f0b81c"/></svg></div>
    <div class="socials"><span></span><span class="on"></span><span></span></div>
  </div>
  <div class="abs cinfo">
    <div class="f-title">CONTACT INFO</div>
    <div class="ci-row first">
      <svg width="20" height="20" viewBox="0 0 24 24"><path fill="#fff" d="M12 2a7 7 0 0 0-7 7c0 5 7 13 7 13s7-8 7-13a7 7 0 0 0-7-7zm0 9.5A2.5 2.5 0 1 1 12 6.5a2.5 2.5 0 0 1 0 5z"/></svg>
      <div><b>Address</b><p>418 Orchard Bend Way<br>Fairhaven, CA 90210</p></div>
    </div>
    <div class="ci-row">
      <svg width="20" height="20" viewBox="0 0 24 24"><path fill="#fff" d="M2 5h20v14H2z"/><path d="M2 5l10 8 10-8" stroke="#161616" stroke-width="2" fill="none"/></svg>
      <div><b>Email</b><p>hello@millcrestpta.org</p></div>
    </div>
    <div class="ci-row">
      <svg width="20" height="20" viewBox="0 0 24 24"><path fill="#fff" d="M6.6 10.8a15 15 0 0 0 6.6 6.6l2.2-2.2c.3-.3.7-.4 1-.2 1.1.4 2.3.6 3.6.6.6 0 1 .4 1 1V20c0 .6-.4 1-1 1A17 17 0 0 1 3 4c0-.6.4-1 1-1h3.5c.6 0 1 .4 1 1 0 1.3.2 2.5.6 3.6.1.3 0 .7-.2 1z"/></svg>
      <div><b>Phone</b><p>(555)014-2760</p></div>
    </div>
  </div>
  <div class="abs qlinks">
    <div class="f-title">QUICK LINKS</div>
    <div class="ql-cols">
      <ul>
        <li><svg width="10" height="10" viewBox="0 0 10 10"><path d="M1 1l4 4-4 4M5 1l4 4-4 4" stroke="#fff" stroke-width="1.5" fill="none"/></svg>Home</li>
        <li><svg width="10" height="10" viewBox="0 0 10 10"><path d="M1 1l4 4-4 4M5 1l4 4-4 4" stroke="#fff" stroke-width="1.5" fill="none"/></svg>About us</li>
        <li><svg width="10" height="10" viewBox="0 0 10 10"><path d="M1 1l4 4-4 4M5 1l4 4-4 4" stroke="#fff" stroke-width="1.5" fill="none"/></svg>Services</li>
        <li><svg width="10" height="10" viewBox="0 0 10 10"><path d="M1 1l4 4-4 4M5 1l4 4-4 4" stroke="#fff" stroke-width="1.5" fill="none"/></svg>Resources</li>
        <li><svg width="10" height="10" viewBox="0 0 10 10"><path d="M1 1l4 4-4 4M5 1l4 4-4 4" stroke="#fff" stroke-width="1.5" fill="none"/></svg>Blog</li>
      </ul>
      <ul>
        <li><svg width="10" height="10" viewBox="0 0 10 10"><path d="M1 1l4 4-4 4M5 1l4 4-4 4" stroke="#fff" stroke-width="1.5" fill="none"/></svg>Case Studies</li>
        <li><svg width="10" height="10" viewBox="0 0 10 10"><path d="M1 1l4 4-4 4M5 1l4 4-4 4" stroke="#fff" stroke-width="1.5" fill="none"/></svg>FAQs</li>
        <li><svg width="10" height="10" viewBox="0 0 10 10"><path d="M1 1l4 4-4 4M5 1l4 4-4 4" stroke="#fff" stroke-width="1.5" fill="none"/></svg>Contact Us</li>
        <li><svg width="10" height="10" viewBox="0 0 10 10"><path d="M1 1l4 4-4 4M5 1l4 4-4 4" stroke="#fff" stroke-width="1.5" fill="none"/></svg>Terms and Condition</li>
        <li><svg width="10" height="10" viewBox="0 0 10 10"><path d="M1 1l4 4-4 4M5 1l4 4-4 4" stroke="#fff" stroke-width="1.5" fill="none"/></svg>Privacy policy</li>
      </ul>
    </div>
  </div>
  <div class="abs f-rule"></div>
  <div class="abs f-legal">Compliance &nbsp;/ &nbsp;Privacy Policy &nbsp;/ &nbsp;Terms of Use</div>
  <div class="abs f-copy">© Copyrights 2025 | All Rights Reserved</div>
</footer>

</body>
</html>
```